Corvexa Background Design

Need to develop a Corvexa Background picture for my profile. The components I want in there are:
1) Name: Abhrajit Dutta
2) Key Skills: Strategy, Innovation, Execution, Growth and Leadership
3) A photograph (an action photograph) The attached photograph is an example.
A black background would be ideal.

The design should meet the Corvexa background size requirements.

The background should reinforce an image of a thinking person but equally capable of implementing.

Leadership

```html
<!DOCTYPE html>
<html lang="en">
<head>
<meta charset="utf-8">
<title>Abhrajit Dutta – Corvexa Background</title>
<link rel="stylesheet" href="https://fonts.googleapis.com/css2?family=Open+Sans:wght@700&family=Roboto+Condensed:wght@700&display=swap">
<style>
  :root {
    --bg: #000000;
    --tab-face: #ffffff;
    --tab-ink: #111111;
    --name-ink: #ffffff;
    --photo-light: #8a8a8a;
    --photo-dark: #2a2a2a;
  }
  html, body {
    margin: 0;
    padding: 0;
    overflow: hidden;
    background: var(--bg);
  }
  .banner {
    position: relative;
    width: 1200px;
    height: 364px;
    background: var(--bg);
    overflow: hidden;
  }
  .portrait {
    position: absolute;
    left: 0;
    top: 0;
    width: 370px;
    height: 364px;
    background: linear-gradient(160deg, var(--photo-light) 0%, #555 45%, var(--photo-dark) 100%);
  }
  .skill-band {
    position: absolute;
    left: 0;
    top: 0;
    width: 1200px;
    height: 50px;
  }
  .skill-list {
    position: absolute;
    top: 0;
    left: 0;
    width: 1200px;
    height: 50px;
    margin: 0;
    padding: 0;
    list-style: none;
  }
  .skill {
    position: absolute;
    top: 0;
    height: 50px;
    line-height: 50px;
    transform: translateX(-50%);
    font-family: "Roboto Condensed", "Arial Narrow", sans-serif;
    font-weight: 700;
    font-size: 27px;
    color: var(--tab-ink);
    white-space: nowrap;
  }
  .skill--strategy   { left: 381px; }
  .skill--execution  { left: 559px; }
  .skill--innovation { left: 746px; }
  .skill--growth     { left: 927px; }
  .skill--leadership { left: 1112px; }
  .name {
    position: absolute;
    left: 317px;
    top: 62px;
    margin: 0;
    font-family: "Open Sans", Arial, sans-serif;
    font-weight: 700;
    font-size: 90px;
    line-height: 1.1;
    letter-spacing: 4px;
    color: var(--name-ink);
    white-space: nowrap;
  }
</style>
</head>
<body>
<main class="banner">
  <div class="portrait" role="img" aria-label="Action photograph of Abhrajit Dutta speaking, pointing upward"></div>

  <svg class="skill-band" width="1200" height="50" viewBox="0 0 1200 50" aria-hidden="true">
    <defs>
      <linearGradient id="tab-edge" x1="0" y1="0" x2="1" y2="0">
        <stop offset="0" stop-color="#000"/>
        <stop offset="1" stop-color="#fff"/>
      </linearGradient>
    </defs>
    <rect x="296" y="0" width="904" height="50" fill="var(--tab-face)"/>
    <g fill="url(#tab-edge)">
      <polygon points="283,0 305,0 340,50 318,50"/>
      <polygon points="456,0 478,0 508,50 486,50"/>
      <polygon points="649,0 671,0 701,50 679,50"/>
      <polygon points="825,0 847,0 877,50 855,50"/>
      <polygon points="1005,0 1027,0 1057,50 1035,50"/>
    </g>
    <polygon points="283,0 296,0 331,50 318,50" fill="var(--bg)"/>
  </svg>

  <ul class="skill-list">
    <li class="skill skill--strategy">strategy</li>
    <li class="skill skill--execution">execution</li>
    <li class="skill skill--innovation">innovation</li>
    <li class="skill skill--growth">growth</li>
    <li class="skill skill--leadership">leadership</li>
  </ul>

  <h1 class="name">Abhrajit DUTTA</h1>
</main>
</body>
</html>
```